Core Values Banner For Hearthwell Guards Inc

We want to take the core values for our small growing chimney service company and post them for our entire team to see on a daily basis. We want to be remind everyone how important this is too us all. IntegrityWe try to be honest and accountable in all aspects of our business, as well as in our personal interactions. We do what we say we will do, when we say we will do it, and how we say we will do it.Kaizen“Change for the best”We strive to constantly grow and improve, both personally and professionally. We own up to our mistakes and strive to resolve and learn from them. We actively seek feedback from our clients and each other. We believe the most innovative ideas come when we intentionally look for them.FamilyWe are a family-owned business, and we consider everyone who works here and every one we serve to be part of the family. Being honest and genuine with each other and our customers is what sets us apart. We put ourselves in our customer’s shoes and make recommendations as if it were our chimney, our home and our family.

Font styles to use
Serif
Sans Serif

Colors
ec1f27

Requirements
Must have
• This banner will be approximately 2.5' in height and 6 to 6.5' in width.
• I would like all 3 core values and there definitions listed on the banner
• check out the feel of our marketing on our website www.hearthwellguardsnx.com

```html
<!DOCTYPE html>
<html lang="en">
<head>
<meta charset="utf-8">
<title>Hearthwell Guards Inc — Core Values Banner</title>
<link href="https://fonts.googleapis.com/css2?family=Lato:wght@400;700;900&display=swap" rel="stylesheet">
<style>
  :root {
    --backdrop: #f4f4f4;
    --value-red: #cf1e3a;
    --kaizen-pink: #d0245a;
    --ink-white: #ffffff;
    --ghost-white: rgba(255, 255, 255, 0.07);
  }
  * { margin: 0; padding: 0; box-sizing: border-box; }
  html, body {
    width: 1200px;
    height: 540px;
    overflow: hidden;
    background: var(--backdrop);
    font-family: "Lato", Arial, sans-serif;
    color: var(--ink-white);
  }
  .values-banner {
    position: absolute;
    left: 60px;
    top: 62px;
    width: 1082px;
    height: 416px;
    display: flex;
    box-shadow: 0 14px 18px rgba(0, 0, 0, 0.18);
  }
  .value-panel {
    position: relative;
    flex: 1;
    background: var(--value-red);
    overflow: hidden;
    text-align: center;
  }
  .value-panel--kaizen {
    background: var(--kaizen-pink);
    z-index: 1;
    box-shadow: 0 0 16px rgba(0, 0, 0, 0.28);
  }
  .ghost-word {
    position: absolute;
    font-weight: 900;
    line-height: 1;
    color: var(--ghost-white);
    white-space: nowrap;
    pointer-events: none;
  }
  .value-panel--integrity .ghost-word { left: 31px; top: -10px; font-size: 78px; }
  .value-panel--kaizen .ghost-word { left: 33px; top: 340px; font-size: 100px; }
  .value-panel--family .ghost-word { left: 34px; top: -16px; font-size: 100px; }
  .value-icon {
    position: absolute;
    left: 50%;
    top: 62px;
    width: 93px;
    height: 93px;
    transform: translateX(-50%);
  }
  .value-title {
    position: absolute;
    left: 0;
    right: 0;
    top: 188px;
    font-weight: 700;
    font-size: 39px;
    letter-spacing: 0.3px;
    line-height: 1;
  }
  .value-panel--kaizen .value-title { top: 176px; }
  .value-tagline {
    position: absolute;
    left: 0;
    right: 0;
    top: 216px;
    font-weight: 700;
    font-size: 22px;
    line-height: 1;
  }
  .value-text {
    position: absolute;
    left: 41px;
    right: 41px;
    top: 263px;
    font-size: 11.6px;
    line-height: 17.4px;
    font-weight: 400;
    text-align: justify;
    text-align-last: center;
    hyphens: auto;
    -webkit-hyphens: auto;
  }
  .value-panel--integrity .value-text { left: 46px; right: 46px; text-align: center; }
  .value-panel--family .value-text { left: 38px; right: 38px; }
</style>
</head>
<body>
  <main class="values-banner">
    <section class="value-panel value-panel--integrity">
      <span class="ghost-word" aria-hidden="true">Integrity</span>
      <svg class="value-icon" viewBox="0 0 94 94" aria-hidden="true">
        <g fill="none" stroke="#fff" stroke-width="3">
          <path d="M38 2H2V92H38M56 2H92V92H56"/>
        </g>
        <g fill="#fff">
          <rect x="45.5" y="24" width="3" height="44"/>
          <circle cx="47" cy="24" r="3"/>
          <rect x="24" y="30" width="46" height="2.5" rx="1"/>
          <path d="M24 32L16 50H18.5L24 37L29.5 50H32Z"/>
          <path d="M70 32L62 50H64.5L70 37L75.5 50H78Z"/>
          <path d="M14 50H34A10 8 0 0 1 14 50Z"/>
          <path d="M60 50H80A10 8 0 0 1 60 50Z"/>
          <path d="M41 68H53L55 73H39Z"/>
          <rect x="34" y="73" width="26" height="4" rx="1"/>
        </g>
      </svg>
      <h2 class="value-title">INTEGRITY</h2>
      <p class="value-text">We try to be honest and accountable in all aspects of our business, as well as in our personal interactions. We do what we say we will do, when we say we will do it, and how we say we will do it.</p>
    </section>

    <section class="value-panel value-panel--kaizen">
      <span class="ghost-word" aria-hidden="true">Kaizen</span>
      <svg class="value-icon" viewBox="0 0 94 94" aria-hidden="true">
        <g fill="none" stroke="#fff" stroke-width="3">
          <path d="M38 2H2V92H38M56 2H92V92H56"/>
          <path d="M25 44A22 22 0 0 1 66 34"/>
          <path d="M69 50A22 22 0 0 1 28 60"/>
        </g>
        <g fill="#fff">
          <path d="M60 30L72 30L68 40Z"/>
          <path d="M34 64L22 64L26 54Z"/>
          <path d="M19 42H31L25 50Z"/>
          <path d="M63 52H75L69 44Z"/>
          <rect x="36" y="50" width="4" height="8"/>
          <rect x="42" y="46" width="4" height="12"/>
          <rect x="48" y="42" width="4" height="16"/>
          <rect x="54" y="38" width="4" height="20"/>
          <path d="M35 46L45 40L50 43L58 34L56 33L61 31L60 36L59 35L50 45L45 42L36 48Z"/>
        </g>
      </svg>
      <h2 class="value-title">KAIZEN</h2>
      <p class="value-tagline">“Change for the best”</p>
      <p class="value-text">We strive to constantly grow and improve, both personally and professionally. We own up to our mistakes and strive to resolve and learn from them. We actively seek feedback from our clients and each other. We believe the most innovative ideas come when we intentionally look for them.</p>
    </section>

    <section class="value-panel value-panel--family">
      <span class="ghost-word" aria-hidden="true">Family</span>
      <svg class="value-icon" viewBox="0 0 94 94" aria-hidden="true">
        <g fill="none" stroke="#fff" stroke-width="3">
          <path d="M38 2H2V92H38M56 2H92V92H56"/>
        </g>
        <g fill="#fff">
          <circle cx="28" cy="42" r="5"/>
          <path d="M19 60V54A5 5 0 0 1 24 49H32A5 5 0 0 1 37 54V60Z"/>
          <circle cx="47" cy="40" r="5.5"/>
          <path d="M37.5 60V53A5.5 5.5 0 0 1 43 47.5H51A5.5 5.5 0 0 1 56.5 53V60Z"/>
          <circle cx="66" cy="42" r="5"/>
          <path d="M57 60V54A5 5 0 0 1 62 49H70A5 5 0 0 1 75 54V60Z"/>
        </g>
      </svg>
      <h2 class="value-title">FAMILY</h2>
      <p class="value-text">We are a family-owned business, and we consider everyone who works here and every one we serve to be part of the family. Being honest and genuine with each other and our customers is what sets us apart. We put ourselves in our customer’s shoes and make recommendations as if it were our chimney, our home and our family.</p>
    </section>
  </main>
</body>
</html>
```